-Photo booth rental Web Design Project

Our business is a small photo booth rental service serving the capital region and surrounding areas. The photo booth is a portable booth that fits up to 10 guest. I am looking for a website that will have social media capabilities and also private log ins for clients to view their photo albums online after their event. We provide full service photo booth rentals for all types of parties. I am looking for something fun and unique but also professional and I am also looking to maybe somehow incorporate the age of the photo booth which was invented in 1888. I do not have the photos of our photo booth available because we are just starting up and I wanted to get everything together first but I will provide stock photo booth pictures .Thank you for your patience i know it wont be an easy task with out those things. I added a word document describing information i will need on our website, i am looking for a home page, contact us and book an event page, online gallery page, and pricing. If you need any more information please feel free to contact me. Thanks for your help and I look forward to working with you.

Target Market(s)

For everyone from brides to be for their weddings or private parties, corporate parties, school dances, charity events, community events ect

Industry/Entity Type

Business

Requirements
Nice to have
• social media sharing

```html
<!DOCTYPE html>
<html lang="en">
<head>
<meta charset="utf-8">
<title>Jolly Frames Photo Booth</title>
<link href="https://fonts.googleapis.com/css2?family=Questrial&family=Cabin:wght@600;700&display=swap" rel="stylesheet">
<style>
:root{
  --wood:#2f1d14;
  --wood-deep:#24160f;
  --wood-mid:#3a2519;
  --tan:#a5825f;
  --tan-light:#c9ad8e;
  --cream:#f1ece6;
  --paper:#f3f3f3;
  --ink:#4a3a30;
  --muted:#8a7d74;
  --line:#e3e0dd;
  --btn:#3b2217;
  --blush:#dcc3b8;
  --white:#ffffff;
}
*{box-sizing:border-box;margin:0;padding:0}
html,body{width:1200px;height:2497px;overflow:hidden}
body{position:relative;background:var(--paper);font-family:"Questrial",sans-serif;color:var(--ink)}
.abs{position:absolute}

/* header */
.topline{left:0;top:0;width:1200px;height:6px;background:var(--wood)}
.header{left:0;top:6px;width:1200px;height:216px;background:#efefef}
.brand{left:160px;top:48px;display:flex;align-items:center;gap:12px}
.brand-dot{width:14px;height:14px;border-radius:50%;background:var(--tan)}
.brand-name{font-size:30px;line-height:32px;color:var(--ink)}
.phone{right:160px;top:30px;font-size:24px;color:var(--tan)}
.nav{right:160px;top:94px;display:flex;gap:37px;font-size:14px;color:var(--muted)}
.nav .active{color:var(--ink)}

/* hero */
.wood-band{left:0;top:222px;width:1200px;height:722px;background:linear-gradient(90deg,#2a1911,#3a251a 30%,#2d1c13 55%,#3a2519 80%,#2a1911)}
.slider{left:160px;top:160px;width:880px;height:452px;background:var(--white);padding:8px;box-shadow:0 8px 24px rgba(0,0,0,.5)}
.slide{width:100%;height:100%;background:linear-gradient(120deg,#c9b48a,#8e8a5c 45%,#d9d0b3 75%,#f2ece0)}
.arrow{width:40px;height:40px;background:var(--white);top:370px;display:flex;align-items:center;justify-content:center}
.arrow.left{left:140px}.arrow.right{left:1020px}

.feature{top:670px;width:280px;text-align:center}
.feature h3,.sec-title{font-weight:400;font-size:21px;color:var(--cream)}
.feature h3 span,.sec-title span{color:var(--tan)}
.orn{display:block;margin:12px auto 0;width:72px;height:12px;background:var(--tan);opacity:.55;border-radius:6px}
.feature p{margin-top:22px;font-size:11.5px;line-height:17px;color:#d8cfc6}
.btn-ghost{display:inline-block;margin-top:24px;width:123px;height:38px;line-height:36px;border:1px solid #a89a8e;color:#e8e1da;font-size:12px;text-align:center}

/* second band */
.media-band{left:0;top:944px;width:1200px;height:460px;background:linear-gradient(90deg,#311f15,#3d271b 40%,#34211673,#3a2519 100%),var(--wood-mid)}
.video{left:160px;top:1033px;width:341px;height:175px;border:1px solid #7a6a5e;padding:4px}
.video-fill{width:100%;height:100%;background:linear-gradient(90deg,#d9c7b3 0%,#8e2e22 40%,#7a2118 60%,#3a3a3a 75%,#2b2b2b)}
.play{left:305px;top:1094px;width:52px;height:52px;border-radius:50%;border:3px solid var(--white);background:rgba(0,0,0,.35);display:flex;align-items:center;justify-content:center}
.video-text{left:160px;top:1236px;width:345px;font-size:11.5px;line-height:17px;color:#d8cfc6}

.tile{width:156px;height:153px;border:1px solid #8a7a6e;padding:3px;background:rgba(255,255,255,.05)}
.tile-img{width:100%;height:108px}
.tile-label{display:flex;justify-content:space-between;align-items:center;height:36px;padding:0 8px;color:#f1ece6;font-size:12px}
.tile-go{width:16px;height:16px;border-radius:50%;background:#24160f;display:flex;align-items:center;justify-content:center}

/* pricing */
.pricing-title{left:0;top:1422px;width:1200px;text-align:center;font-size:26px;color:var(--ink)}
.pricing-title span{color:var(--tan)}
.orn-dark{left:568px;top:1466px;width:64px;height:12px;background:var(--ink);opacity:.5;border-radius:6px}
.card{top:1503px;width:271px;height:399px;background:var(--white);box-shadow:0 2px 6px rgba(0,0,0,.15)}
.card-head{position:relative;height:87px;text-align:center;color:var(--white);padding-top:14px}
.card-head .pk{font-size:22px;line-height:24px}
.card-head .tier{font-family:"Cabin",sans-serif;font-weight:700;font-size:31px;line-height:34px;letter-spacing:.5px}
.card-head::after{content:"";position:absolute;left:50%;bottom:-14px;margin-left:-15px;border-left:15px solid transparent;border-right:15px solid transparent;border-top:15px solid var(--hd)}
.h1{--hd:#a07e5e;background:var(--hd)}
.h2{--hd:#2a1911;background:var(--hd)}
.h3{--hd:#3e2418;background:var(--hd)}
.features{list-style:none;padding:8px 10px 0}
.features li{display:flex;gap:10px;align-items:flex-start;border-bottom:1px solid var(--line);padding:10px 2px 9px;font-size:12.5px;line-height:16px;color:var(--muted)}
.features svg{flex:none;margin-top:2px}
.price{text-align:center;margin-top:16px;font-family:"Cabin",sans-serif;font-weight:700;font-size:46px;line-height:56px}
.price.tan{color:#a07e5e}.price.dark{color:#2a1911}
.btn-solid{position:absolute;left:50%;margin-left:-85px;bottom:-16px;width:170px;height:36px;line-height:36px;background:var(--btn);color:var(--white);font-size:12px;text-align:center}

/* add-on ribbon */
.white-band{left:0;top:2030px;width:1200px;height:364px;background:var(--white)}
.ribbon{left:166px;top:1983px;width:866px;height:89px}
.ribbon-text{left:213px;top:2015px;font-size:16px;color:var(--ink)}
.ribbon-deal{left:825px;top:2016px;font-family:"Cabin",sans-serif;font-weight:700;font-size:16px;color:var(--white)}

/* info columns */
.col{top:2120px}
.col h4{font-weight:400;font-size:21px;color:var(--ink)}
.col h4 span{color:var(--tan)}
.events{list-style:none;margin-top:16px}
.events li{position:relative;padding-left:16px;font-size:12px;line-height:24px;color:var(--muted)}
.events li::before{content:"";position:absolute;left:0;top:10px;width:5px;height:5px;border-radius:50%;background:var(--tan)}
.col p{margin-top:16px;font-size:11.5px;line-height:20px;color:var(--muted)}
.quote{font-style:italic}
.author{margin-top:14px;font-size:14px;color:var(--tan);font-style:italic}

/* footer */
.footer{left:0;top:2394px;width:1200px;height:103px;background:var(--wood-deep)}
.social{left:176px;top:2429px;display:flex;gap:9px}
.social span{width:30px;height:30px;border-radius:50%;border:1px solid #d8cfc6}
.copy{right:162px;top:2426px;font-size:10px;color:#bfb3a8;text-align:right}
.foot-nav{right:162px;top:2445px;display:flex;gap:12px;font-size:12px;color:#e6dfd8}
.version{left:1102px;top:2444px;font-size:11px;color:#bfb3a8}
</style>
</head>
<body>

<div class="abs topline"></div>
<header class="abs header"></header>
<div class="abs brand">
  <span class="brand-name">Jolly Frames<br>photo booth</span>
  <span class="brand-dot"></span>
</div>
<div class="abs phone">Call +44 (0) 1632 960418</div>
<nav class="abs nav">
  <span class="active">Home</span><span>Pricing</span><span>Contact us</span><span>Book an Event</span><span>Client log in</span>
</nav>

<section class="abs wood-band"></section>
<div class="abs slider"><div class="slide" role="img" aria-label="Photographer capturing a smiling wedding party outdoors"></div></div>
<div class="abs arrow left"><svg width="10" height="16" viewBox="0 0 10 16"><path d="M8 1 2 8l6 7" fill="none" stroke="#999" stroke-width="1.5"/></svg></div>
<div class="abs arrow right"><svg width="10" height="16" viewBox="0 0 10 16"><path d="M2 1l6 7-6 7" fill="none" stroke="#999" stroke-width="1.5"/></svg></div>

<div class="abs feature" style="left:146px">
  <h3><span>View/Sign</span> Contracts</h3>
  <span class="orn" role="img" aria-label="Small flourish ornament"></span>
  <p>Review and sign your booking agreement online in a few minutes, then keep a copy of every detail for your event day.</p>
  <span class="btn-ghost">VIEW MORE</span>
</div>
<div class="abs feature" style="left:459px">
  <h3><span>View Picture</span> Gallery</h3>
  <span class="orn" role="img" aria-label="Small flourish ornament"></span>
  <p>Browse the photos from your party in a private album, pick your favourites and relive the fun with friends and family anytime.</p>
  <span class="btn-ghost">VIEW MORE</span>
</div>
<div class="abs feature" style="left:772px">
  <h3><span>Upload/share</span> Gallery</h3>
  <span class="orn" role="img" aria-label="Small flourish ornament"></span>
  <p>Upload extra snaps from your guests, collect them in one shared album and post the best moments straight to your social pages.</p>
  <span class="btn-ghost">VIEW MORE</span>
</div>

<section class="abs media-band"></section>
<h3 class="abs sec-title" style="left:160px;top:980px"><span>Video</span> Booth</h3>
<div class="abs video"><div class="video-fill" role="img" aria-label="Couple posing in front of the photo booth"></div></div>
<div class="abs play"><svg width="18" height="20" viewBox="0 0 18 20"><path d="M2 1l15 9-15 9z" fill="#fff"/></svg></div>
<p class="abs video-text">Our Booths feature the latest equipment and technology with Smart-Touch screens, FriendNet and email uploading, TunePod ready speaker systems.</p>
<span class="abs btn-ghost" style="left:160px;top:1289px;margin-top:0">VIEW MORE</span>

<h3 class="abs sec-title" style="left:539px;top:980px"><span>Our</span> Recent Photos</h3>

<div class="abs tile" style="left:539px;top:1033px"><div class="tile-img" role="img" aria-label="Wedding couple photo" style="background:linear-gradient(135deg,#9ab57a,#e8e4da)"></div><div class="tile-label">Weddings<span class="tile-go"><svg width="6" height="8" viewBox="0 0 6 8"><path d="M1 0l5 4-5 4z" fill="#fff"/></svg></span></div></div>
<div class="abs tile" style="left:712px;top:1033px"><div class="tile-img" role="img" aria-label="Kids at a birthday party photo" style="background:linear-gradient(135deg,#9ccad8,#c98b5c)"></div><div class="tile-label">Birthday parties<span class="tile-go"><svg width="6" height="8" viewBox="0 0 6 8"><path d="M1 0l5 4-5 4z" fill="#fff"/></svg></span></div></div>
<div class="abs tile" style="left:885px;top:1033px"><div class="tile-img" role="img" aria-label="Graduates celebrating photo" style="background:linear-gradient(135deg,#6f5e52,#1d1a18)"></div><div class="tile-label">Graduations<span class="tile-go"><svg width="6" height="8" viewBox="0 0 6 8"><path d="M1 0l5 4-5 4z" fill="#fff"/></svg></span></div></div>
<div class="abs tile" style="left:539px;top:1201px"><div class="tile-img" role="img" aria-label="Friends at a holiday party photo" style="background:linear-gradient(135deg,#7a3a24,#e2b47a)"></div><div class="tile-label">Holiday parties<span class="tile-go"><svg width="6" height="8" viewBox="0 0 6 8"><path d="M1 0l5 4-5 4z" fill="#fff"/></svg></span></div></div>
<div class="abs tile" style="left:712px;top:1201px"><div class="tile-img" role="img" aria-label="Champagne toast at a corporate party photo" style="background:linear-gradient(135deg,#2c2a2a,#d9c79a)"></div><div class="tile-label">Corporate parties<span class="tile-go"><svg width="6" height="8" viewBox="0 0 6 8"><path d="M1 0l5 4-5 4z" fill="#fff"/></svg></span></div></div>
<div class="abs tile" style="left:885px;top:1201px"><div class="tile-img" role="img" aria-label="Bar mitzvah celebration photo" style="background:linear-gradient(135deg,#e8e0d4,#7a2a2a)"></div><div class="tile-label">Cbar/ bat<span class="tile-go"><svg width="6" height="8" viewBox="0 0 6 8"><path d="M1 0l5 4-5 4z" fill="#fff"/></svg></span></div></div>

<h2 class="abs pricing-title" style="font-weight:400"><span>Pricing</span> Information</h2>
<span class="abs orn-dark" role="img" aria-label="Small flourish ornament"></span>

<div class="abs card" style="left:160px">
  <div class="card-head h1"><div class="pk">Package 1</div><div class="tier">STANDARD</div></div>
  <ul class="features">
    <li><svg width="12" height="10" viewBox="0 0 12 10"><path d="M1 5l3.5 3.5L11 1.5" fill="none" stroke="#bbb" stroke-width="2"/></svg>3 hours of service</li>
    <li><svg width="12" height="10" viewBox="0 0 12 10"><path d="M1 5l3.5 3.5L11 1.5" fill="none" stroke="#bbb" stroke-width="2"/></svg>Set up &amp; removal</li>
    <li><svg width="12" height="10" viewBox="0 0 12 10"><path d="M1 5l3.5 3.5L11 1.5" fill="none" stroke="#bbb" stroke-width="2"/></svg>Professional &amp; friendly<br>booth attendant</li>
    <li><svg width="12" height="10" viewBox="0 0 12 10"><path d="M1 5l3.5 3.5L11 1.5" fill="none" stroke="#bbb" stroke-width="2"/></svg>Dvd or usb flash drive of picture</li>
    <li><svg width="12" height="10" viewBox="0 0 12 10"><path d="M1 5l3.5 3.5L11 1.5" fill="none" stroke="#bbb" stroke-width="2"/></svg>Guestbook</li>
  </ul>
  <div class="price tan">$675</div>
  <span class="btn-solid">VIEW MORE</span>
</div>
<div class="abs card" style="left:464px">
  <div class="card-head h2"><div class="pk">Package 2</div><div class="tier">ULTIMATE</div></div>
  <ul class="features">
    <li><svg width="12" height="10" viewBox="0 0 12 10"><path d="M1 5l3.5 3.5L11 1.5" fill="none" stroke="#bbb" stroke-width="2"/></svg>3 hours of service</li>
    <li><svg width="12" height="10" viewBox="0 0 12 10"><path d="M1 5l3.5 3.5L11 1.5" fill="none" stroke="#bbb" stroke-width="2"/></svg>Set up &amp; removal</li>
    <li><svg width="12" height="10" viewBox="0 0 12 10"><path d="M1 5l3.5 3.5L11 1.5" fill="none" stroke="#bbb" stroke-width="2"/></svg>Professional &amp; friendly<br>booth attendant</li>
    <li><svg width="12" height="10" viewBox="0 0 12 10"><path d="M1 5l3.5 3.5L11 1.5" fill="none" stroke="#bbb" stroke-width="2"/></svg>Dvd or usb flash drive of picture</li>
    <li><svg width="12" height="10" viewBox="0 0 12 10"><path d="M1 5l3.5 3.5L11 1.5" fill="none" stroke="#bbb" stroke-width="2"/></svg>Guestbook</li>
  </ul>
  <div class="price dark">$850</div>
  <span class="btn-solid">VIEW MORE</span>
</div>
<div class="abs card" style="left:764px">
  <div class="card-head h3"><div class="pk">Package 3</div><div class="tier">EXTREME</div></div>
  <ul class="features">
    <li><svg width="12" height="10" viewBox="0 0 12 10"><path d="M1 5l3.5 3.5L11 1.5" fill="none" stroke="#bbb" stroke-width="2"/></svg>3 hours of service</li>
    <li><svg width="12" height="10" viewBox="0 0 12 10"><path d="M1 5l3.5 3.5L11 1.5" fill="none" stroke="#bbb" stroke-width="2"/></svg>Set up &amp; removal</li>
    <li><svg width="12" height="10" viewBox="0 0 12 10"><path d="M1 5l3.5 3.5L11 1.5" fill="none" stroke="#bbb" stroke-width="2"/></svg>Professional &amp; friendly<br>booth attendant</li>
    <li><svg width="12" height="10" viewBox="0 0 12 10"><path d="M1 5l3.5 3.5L11 1.5" fill="none" stroke="#bbb" stroke-width="2"/></svg>Dvd or usb flash drive of picture</li>
    <li><svg width="12" height="10" viewBox="0 0 12 10"><path d="M1 5l3.5 3.5L11 1.5" fill="none" stroke="#bbb" stroke-width="2"/></svg>Guestbook</li>
  </ul>
  <div class="price dark">$975</div>
  <span class="btn-solid">VIEW MORE</span>
</div>

<section class="abs white-band"></section>
<svg class="abs ribbon" viewBox="0 0 866 89" aria-hidden="true">
  <path d="M0 0h866l-22 44 22 45H0l22-45z" fill="#ead8d0"/>
  <path d="M10 6h846l-18 38 18 39H10l18-39z" fill="#d6b9ad"/>
  <path d="M640 6h216l-18 38 18 39H640z" fill="#6a4a3c"/>
</svg>
<div class="abs ribbon-text">Add on’s: magnet photo strip frames, stand up acrylic photo strip frames</div>
<div class="abs ribbon-deal">ONLY $100 DEPOSIT</div>

<div class="abs col" style="left:160px;width:260px">
  <h4><span>Recent</span> Events</h4>
  <ul class="events">
    <li>weddings, birthday parties, graduations,</li>
    <li>holiday parties, corporate parties,</li>
    <li>bar/ bat mitzvahs, bridal showers,</li>
    <li>baby showers, anniversaries,</li>
    <li>grand openings, school events, proms,</li>
    <li>corporate events, promotional events,</li>
    <li>trade shows, conventions,</li>
    <li>community &amp; charity events</li>
  </ul>
</div>
<div class="abs col" style="left:459px;width:280px">
  <h4><span>Welcome to</span> Jolly Frames</h4>
  <p>We are a family owned and operated photo booth rental company serving Columbia, Greene, Albany &amp; surrounding counties to create fun &amp; memorable memories for any type of event.</p>
  <p>Every booking includes set up, a friendly attendant and prints in seconds, so you can relax and enjoy the party with your guests.</p>
</div>
<div class="abs col" style="left:774px;width:266px">
  <h4><span>Client</span> Testimonials</h4>
  <p class="quote">“ The booth was the hit of our wedding. Guests lined up all night, the attendant was friendly and our album was online the very next morning. We will book again.</p>
  <div class="author">Jane Doe, city name lorem ipsum</div>
</div>

<footer class="abs footer"></footer>
<div class="abs social" aria-label="Social links"><span></span><span></span><span></span><span></span></div>
<div class="abs copy">Copyright © 2014 jolly frames photo booth all rights are reserved</div>
<nav class="abs foot-nav"><span>Home</span><span>Pricing</span><span>contact us</span><span>book an event</span><span>Client log in</span></nav>
<div class="abs version">C4</div>

</body>
</html>
```